Non Profit Company Looking For New Website

The website for Fernvale Quillstone Heritage Society should offer the viewer beautiful photos that inspire condifence and joy and tap into our love of horses.

We would like to see a website that displays trust, quality and confidence. Needs to be responsive and mobile friendly for all browsers and coded for both Android & IOS.

READ ATTACHED WEBSITE TEMPLATE FOR COMPLETE DETAILS ON WHAT WE ARE LOOKING FOR.

Looking for recommmendations if we should use WordPress/WooCommerce for site or Wordpress with Shopify Plug in or just Shopify.

Must be both desktop and mobile friendly with fast page load speed. Need the ability to edit ourselves.

Industry/Entity Type

Non Profit

Coding

Coded - Design and coding required

Number of Pages Required

5+ page

Requirements
Must have
• We would like to see a website that displays trust, quality and confidence. Needs to be responsive and mobile friendly for all browsers and coded for both Android & IOS.

Looking for recommendations if we should use WordPress/WooCommerce for site or Wordpress with Shopify Plug in or just Shopify.

Logo Colour:
Pantone 7621 C

READ TEMPLATE THAT IS ATTACHED
Nice to have
• Like look of this website as a sample:
https://www.quellbrimtorva.com/

Another similar non profit organization
https://pellaworthcindle.com/

```html
<!DOCTYPE html>
<html lang="en">
<head>
<meta charset="utf-8">
<title>Fernvale Quillstone Heritage Society</title>
<link href="https://fonts.googleapis.com/css2?family=EB+Garamond:wght@500;600&family=Roboto:wght@400;500;700&display=swap" rel="stylesheet">
<style>
:root{
  --brand:#ad1f2b;
  --brand-dark:#961a25;
  --ink:#222;
  --text:#555;
  --light:#f4f4f4;
  --field:#efefef;
  --footer:#2b2b2b;
  --white:#fff;
}
*{box-sizing:border-box;margin:0;padding:0}
html,body{width:1200px;height:3564px;overflow:hidden}
body{font-family:'Roboto',Arial,sans-serif;color:var(--text);background:var(--white);position:relative}
.serif{font-family:'EB Garamond',Georgia,serif}
section,header,footer{position:absolute;left:0;width:1200px}
.abs{position:absolute}

/* header */
.site-header{top:0;height:93px;background:var(--white);border-top:4px solid var(--brand);z-index:3}
.logo-badge{position:absolute;left:111px;top:0;width:186px;height:148px}
.logo-badge svg{position:absolute;inset:0}
.logo-name{position:absolute;left:0;right:0;top:42px;text-align:center;font-family:'EB Garamond',Georgia,serif;font-weight:500;color:var(--brand);font-size:19px;line-height:23px;letter-spacing:1px}
.main-nav{position:absolute;top:38px;left:0;font-size:14px;font-weight:500;color:var(--ink)}
.main-nav a{position:absolute;white-space:nowrap;color:inherit;text-decoration:none}
.main-nav a.active{color:var(--brand)}

/* hero */
.hero{top:93px;height:599px;background:linear-gradient(160deg,#6f7a2a 0%,#3f4a1c 35%,#2b331a 60%,#5d7a2c 85%,#8aa04a 100%)}
.hero-title{left:111px;top:242px;width:445px;color:var(--white);font-size:33px;line-height:36px;font-weight:500}
.dot{width:13px;height:13px;border:2px solid var(--white);border-radius:50%;left:1141px}
.dot.on::after{content:"";position:absolute;left:2px;top:2px;width:5px;height:5px;border-radius:50%;background:var(--white)}

/* band */
.band{top:692px;height:192px;background:var(--brand)}
.band-art{left:25px;top:35px;width:556px;height:122px;background:linear-gradient(90deg,rgba(255,255,255,.22),rgba(255,255,255,.12));border-radius:4px}
.band h2{left:668px;top:40px;color:var(--white);font-size:37px;font-weight:600}
.band p{left:669px;top:102px;width:420px;color:var(--white);font-size:14.5px;line-height:24px}

/* about */
.about{top:884px;height:417px;text-align:center}
.section-title{color:var(--brand);font-size:40px;font-weight:600;width:100%;text-align:center}
.about .section-title{top:65px}
.about p{left:200px;width:800px;font-size:14.5px;line-height:24px}
.btn{position:absolute;display:flex;align-items:center;justify-content:center;gap:8px;font-weight:700;font-size:14.5px;text-transform:uppercase;border-radius:3px}
.btn-outline{border:2px solid var(--brand);color:var(--brand);background:var(--white)}
.btn-solid{background:var(--brand);color:var(--white)}
.btn-white{background:var(--white);color:var(--brand)}

/* adopt */
.adopt{top:1301px;height:941px;background:var(--light)}
.adopt .section-title{top:33px}
.horse-card{width:352px;height:274px;background:var(--white);padding:4px;box-shadow:0 2px 10px rgba(0,0,0,.12)}
.horse-card .ph{width:100%;height:100%}

/* give */
.give{top:2242px;height:449px;background:linear-gradient(90deg,#5b3a22 0%,#7a5a3a 18%,#d8d4c8 30%,#536b2b 50%,#3f5a1e 75%,#5a7a2a 100%)}
.give h2{left:660px;width:418px;top:100px;text-align:center;color:var(--white);font-size:40px;font-weight:600}
.give p{left:655px;width:430px;top:168px;text-align:center;color:var(--white);font-size:15px;line-height:24px}

/* contact */
.contact{top:2691px;height:556px}
.contact .section-title{top:92px}
.info-icon{width:50px;height:50px;border:2px solid var(--brand);border-radius:50%;left:100px;display:flex;align-items:center;justify-content:center}
.info-title{left:172px;color:var(--ink);font-weight:500;font-size:16px}
.info-text{left:172px;width:330px;font-size:15px;line-height:25px}
.field{background:var(--field);border:1px solid #e2e2e2;font-size:12px;color:#666;display:flex;align-items:center;gap:6px;padding-left:18px}
.field.area{align-items:flex-start;padding-top:38px}

/* footer */
.site-footer{top:3247px;height:317px;background:var(--footer);color:#ddd}
.foot-logo{left:120px;width:190px;top:70px;text-align:center;font-family:'EB Garamond',Georgia,serif;color:var(--brand);font-size:20px;line-height:24px;font-weight:500;letter-spacing:1px}
.social{width:26px;height:26px;border:1.5px solid #ddd;border-radius:50%}
.foot-h{color:var(--white);font-size:13px;font-weight:700;text-transform:uppercase}
.foot-link{font-size:12px;color:#ccc}
.sub-input{left:703px;top:150px;width:266px;height:47px;border-radius:24px;background:var(--white);color:#666;font-size:12px;display:flex;align-items:center;padding-left:20px}
.sub-btn{left:977px;top:150px;width:111px;height:47px;border-radius:24px;background:var(--brand);color:var(--white);font-weight:700;font-size:15px;display:flex;align-items:center;justify-content:center}
.copyright{top:280px;width:100%;text-align:center;font-size:11px;color:#ccc}
</style>
</head>
<body>

<header class="site-header">
  <div class="logo-badge">
    <svg width="186" height="148" viewBox="0 0 186 148"><polygon points="0,0 186,0 186,89 158,144 28,144 0,89" fill="#fff"/></svg>
    <div class="logo-name">FERNVALE<br>QUILLSTONE</div>
  </div>
  <nav class="main-nav">
    <a class="active" style="left:493px">HOME</a>
    <a style="left:575px">ABOUT</a>
    <a style="left:662px">ADOPT</a>
    <a style="left:749px">HORSES</a>
    <a style="left:845px">DONATE</a>
    <a style="left:941px">SHOP</a>
    <a style="left:1020px">CONTACT</a>
  </nav>
</header>

<section class="hero" role="img" aria-label="Two riders on grey horses walking through a sunlit green meadow">
  <h1 class="abs hero-title serif">We support and develop retired thoroughbred racehorses for their next chapter in life</h1>
  <span class="abs dot" style="top:259px"></span>
  <span class="abs dot on" style="top:284px"></span>
  <span class="abs dot" style="top:311px"></span>
</section>

<section class="band">
  <div class="abs band-art" role="img" aria-label="White silhouettes of a racehorse with jockey, a harness horse with sulky and a ridden horse"></div>
  <h2 class="abs serif">Retire. Retrain. Rehome.</h2>
  <p class="abs">Fernvale Quillstone Heritage Society (FQHS) is a registered not-for-profit organization in Fernvale County.</p>
</section>

<section class="about">
  <h2 class="abs section-title serif">What is Thoroughbred Aftercare?</h2>
  <p class="abs" style="top:133px">The health, safety and welfare of our equine athletes does not end at the finish line, and retirement and aftercare are critical to the success of the racing industry.</p>
  <p class="abs" style="top:190px">Aftercare is the safe placement of racehorses after their careers as racehorse are completed. Some horses might retire to the breeding shed or broodmare bands, while others are retrained for second careers.</p>
  <a class="btn btn-outline" style="left:480px;top:273px;width:240px;height:48px">Learn more about us
    <svg width="14" height="14" viewBox="0 0 14 14"><circle cx="7" cy="7" r="7" fill="#ad1f2b"/><path d="M5.5 4l3 3-3 3" stroke="#fff" stroke-width="1.8" fill="none"/></svg></a>
</section>

<section class="adopt">
  <h2 class="abs section-title serif">Adopt a Horse</h2>
  <div class="abs horse-card" style="left:53px;top:126px"><div class="ph" role="img" aria-label="Chestnut horse with white legs trotting in a field" style="background:linear-gradient(180deg,#b9cde0,#8a6a45 55%,#7c8a4a)"></div></div>
  <div class="abs horse-card" style="left:423px;top:126px"><div class="ph" role="img" aria-label="Black horse grazing on green grass" style="background:linear-gradient(180deg,#8a8a6a,#2a2a28 45%,#5f9a3a)"></div></div>
  <div class="abs horse-card" style="left:794px;top:126px"><div class="ph" role="img" aria-label="Two dark horses in a pasture before a farm barn" style="background:linear-gradient(180deg,#f0d3b5,#c7a889 40%,#4a3a2a 60%,#7a8a3a)"></div></div>
  <div class="abs horse-card" style="left:53px;top:423px"><div class="ph" role="img" aria-label="Horse standing in an open field at dawn" style="background:linear-gradient(180deg,#e8e6ea,#d6cfc9 50%,#7a7040)"></div></div>
  <div class="abs horse-card" style="left:423px;top:423px"><div class="ph" role="img" aria-label="Chestnut horse standing among autumn trees" style="background:linear-gradient(180deg,#5a6a30,#a5692f 50%,#b8a25a)"></div></div>
  <div class="abs horse-card" style="left:794px;top:423px"><div class="ph" role="img" aria-label="Chestnut horse standing in a dry meadow" style="background:linear-gradient(180deg,#d8d6d0,#b05a25 50%,#8a7a4a)"></div></div>
  <a class="btn btn-solid" style="left:522px;top:784px;width:156px;height:53px">Adopt now
    <svg width="14" height="14" viewBox="0 0 14 14"><circle cx="7" cy="7" r="7" fill="#fff"/><path d="M5.5 4l3 3-3 3" stroke="#ad1f2b" stroke-width="1.8" fill="none"/></svg></a>
</section>

<section class="give" role="img" aria-label="Rider in a helmet standing beside a bay horse in front of green trees">
  <h2 class="abs serif">Make a Difference</h2>
  <p class="abs">Lorem ipsum dolor sit amet, consectetur adipiscing elit, sed do eiusmod tempor incididunt ut labore et dolore magna aliqua. Ut enim ad minim veniam, quis nostrud exercitation ullamco laboris nisi ut aliquip ex ea commodo consequat.</p>
  <a class="btn btn-white" style="left:765px;top:293px;width:208px;height:45px">More ways to give
    <svg width="14" height="14" viewBox="0 0 14 14"><circle cx="7" cy="7" r="7" fill="#ad1f2b"/><path d="M5.5 4l3 3-3 3" stroke="#fff" stroke-width="1.8" fill="none"/></svg></a>
</section>

<section class="contact">
  <h2 class="abs section-title serif">Have Question or more Information?</h2>

  <div class="abs info-icon" style="top:191px"><svg width="22" height="22" viewBox="0 0 24 24" fill="none" stroke="#ad1f2b" stroke-width="1.5"><path d="M12 22s7-7.5 7-13a7 7 0 0 0-14 0c0 5.5 7 13 7 13z"/><circle cx="12" cy="9" r="2.5"/></svg></div>
  <div class="abs info-title" style="top:192px">Address</div>
  <div class="abs info-text" style="top:220px">123, Lorem ipsum dolor sit amet, consectetur adipiscing elit, sed do</div>

  <div class="abs info-icon" style="top:287px"><svg width="22" height="22" viewBox="0 0 24 24" fill="none" stroke="#ad1f2b" stroke-width="1.5"><path d="M5 3h4l2 5-2.5 1.5a11 11 0 0 0 6 6L16 13l5 2v4a2 2 0 0 1-2 2A17 17 0 0 1 3 5a2 2 0 0 1 2-2z"/></svg></div>
  <div class="abs info-title" style="top:294px">Phone Number</div>
  <div class="abs info-text" style="top:318px">888 888 8888</div>

  <div class="abs info-icon" style="top:369px"><svg width="22" height="22" viewBox="0 0 24 24" fill="none" stroke="#ad1f2b" stroke-width="1.5"><rect x="3" y="5" width="18" height="14"/><path d="M3 5l9 8 9-8M3 19l7-7M21 19l-7-7"/></svg></div>
  <div class="abs info-title" style="top:373px">Email</div>
  <div class="abs info-text" style="top:398px">info@fernvalequillstone.org</div>

  <div class="abs field" style="left:559px;top:186px;width:248px;height:44px">&#9786; Name</div>
  <div class="abs field" style="left:839px;top:186px;width:248px;height:44px">&#9990; Phone Number</div>
  <div class="abs field" style="left:559px;top:244px;width:248px;height:44px">&#9993; Email Address</div>
  <div class="abs field" style="left:839px;top:244px;width:248px;height:44px">&#9998; Subject</div>
  <div class="abs field area" style="left:559px;top:301px;width:527px;height:84px">&#9998; Messagge</div>
  <a class="btn btn-solid" style="left:561px;top:417px;width:113px;height:42px;font-size:15px">Submit</a>
</section>

<footer class="site-footer">
  <div class="abs foot-logo">FERNVALE<br>QUILLSTONE</div>
  <span class="abs social" style="left:153px;top:202px"></span>
  <span class="abs social" style="left:185px;top:202px"></span>
  <span class="abs social" style="left:217px;top:202px"></span>
  <span class="abs social" style="left:249px;top:202px"></span>

  <div class="abs foot-h" style="left:371px;top:62px">Company</div>
  <div class="abs foot-link" style="left:372px;top:101px">Home</div>
  <div class="abs foot-link" style="left:372px;top:126px">About</div>
  <div class="abs foot-link" style="left:372px;top:151px">Adopt</div>
  <div class="abs foot-link" style="left:372px;top:176px">Horses</div>
  <div class="abs foot-link" style="left:372px;top:201px">Donate</div>

  <div class="abs foot-h" style="left:522px;top:63px">Information</div>
  <div class="abs foot-link" style="left:523px;top:100px">Terms &amp; Conditions</div>
  <div class="abs foot-link" style="left:523px;top:125px">Privacy Policy</div>
  <div class="abs foot-link" style="left:523px;top:151px">Disclaimer</div>
  <div class="abs foot-link" style="left:523px;top:176px">Site Map</div>

  <div class="abs foot-h" style="left:702px;top:62px">Subscribe our newsletter</div>
  <div class="abs foot-link" style="left:702px;top:98px;width:300px;line-height:18px">Subscribe to our mailing list to receives daily updates direct to your inbox!</div>
  <div class="abs sub-input">Email Address</div>
  <div class="abs sub-btn">SUBSCRIBE</div>

  <div class="abs copyright">Copyrights &copy; Fernvale Quillstone Heritage Society 2021 | Allrights Reserved</div>
</footer>

</body>
</html>
```